Steadfast Corner Vending Needs a Promotional Flyer

Design a one page, one sided 8 1/2" x 11" flyer that can be handed out to potential customers. Please keep printing efficiencies in mind. See attached old flyers and company website (steadfastcornervend.example) for reference of services. I have also attached our current logo.

```html
<!DOCTYPE html>
<html lang="en">
<head>
<meta charset="utf-8">
<title>Steadfast Corner Vending – Flyer</title>
<link rel="stylesheet" href="https://fonts.googleapis.com/css2?family=Montserrat:wght@400;500;600;700;800;900&display=swap">
<style>
:root{
  --navy:#17324a;
  --ink:#1d2b36;
  --blue:#36a2de;
  --band:#55b4e8;
  --red:#e0252b;
  --paper:#ffffff;
  --muted:#3c4852;
  --rule:#d9e3ea;
}
*{margin:0;padding:0;box-sizing:border-box}
html,body{width:800px;height:1200px;overflow:hidden;background:var(--paper)}
body{font-family:'Montserrat',sans-serif;color:var(--ink)}
.flyer{position:relative;width:800px;height:1200px;background:var(--paper);overflow:hidden}

.brand{position:absolute;left:42px;top:58px;display:flex;align-items:center;gap:10px;
  font-weight:800;color:var(--navy);font-size:17px;line-height:1.1;letter-spacing:.3px;text-transform:uppercase}
.brand-mark{width:22px;height:22px;background:var(--navy);flex:none}

.machines{position:absolute;left:335px;top:52px;width:440px;height:400px;border-radius:6px;
  background:linear-gradient(90deg,#2a2d31 0%,#3c4046 44%,#c9231f 52%,#e8352b 80%,#b91c1a 100%)}

.badge{position:absolute;left:255px;top:66px;width:118px;height:118px;border-radius:50%;
  background:var(--red);color:#fff;display:flex;flex-direction:column;align-items:center;justify-content:center;
  transform:rotate(-14deg);text-align:center;box-shadow:0 2px 6px rgba(0,0,0,.2)}
.badge-small{font-size:11px;font-weight:800;color:#ffd84a;line-height:1.05;text-transform:uppercase}
.badge-big{font-size:22px;font-weight:900;line-height:.95;text-transform:uppercase}

.welcome{position:absolute;left:42px;top:196px;height:30px;padding:0 34px 0 10px;background:var(--ink);color:#fff;
  font-weight:600;font-size:16px;letter-spacing:4px;line-height:30px;
  clip-path:polygon(0 0,100% 0,calc(100% - 18px) 100%,0 100%)}
.headline{position:absolute;left:40px;top:232px;font-weight:900;text-transform:uppercase;line-height:.98}
.headline .dark{display:block;color:var(--ink);font-size:40px;letter-spacing:-.5px}
.headline .blue{display:block;color:var(--blue);font-size:54px;letter-spacing:-1px}

.tagline{position:absolute;left:42px;top:408px;width:280px;padding-left:12px;border-left:4px solid var(--blue);
  font-size:13px;font-weight:700;line-height:1.25;color:var(--ink)}

.why{position:absolute;left:0;top:520px;width:255px;height:38px;background:var(--band);color:#fff;
  font-weight:800;font-size:21px;line-height:38px;padding-left:42px;text-transform:uppercase;
  border-radius:0 6px 6px 0}

.reasons{position:absolute;top:576px}
.reasons.col-a{left:42px;width:170px}
.reasons.col-b{left:222px;width:183px;border-left:1px solid var(--rule);padding-left:10px;height:520px}
.reason{margin-bottom:18px}
.reason h3{font-size:13px;font-weight:700;color:var(--blue);display:flex;align-items:center;gap:4px;margin-bottom:3px;white-space:nowrap}
.reason h3 svg{width:12px;height:12px;flex:none}
.reason p{font-size:10.8px;line-height:1.27;color:var(--muted);font-weight:400}

.call{position:absolute;left:42px;top:1120px;font-size:20px;font-weight:600;color:var(--ink);display:flex;align-items:center;gap:8px;white-space:nowrap}
.call svg{width:18px;height:18px;margin-left:8px}
.call strong{font-weight:600}

.services{position:absolute;left:413px;top:488px;width:345px;height:712px;background:var(--navy);
  border-radius:14px 14px 0 0;color:#fff;padding:30px 24px 0 24px}
.services h2{font-size:31px;font-weight:500;letter-spacing:-.3px;margin-bottom:18px}
.services h2 strong{color:var(--blue);font-weight:800}
.service{display:flex;gap:14px;padding-bottom:22px;margin-bottom:22px;border-bottom:1.5px dotted rgba(85,180,232,.7)}
.service:last-of-type{border-bottom:none}
.service svg{width:50px;height:54px;flex:none;margin-top:4px}
.service h3{font-size:22px;font-weight:700;margin-bottom:6px;white-space:nowrap}
.service p{font-size:11.2px;line-height:1.3;font-weight:400;color:#e6eef4}
.brands{display:grid;grid-template-columns:auto auto;justify-content:start;gap:3px 16px;margin-top:12px;list-style:none}
.brands li{font-size:10.5px;font-weight:600;display:flex;align-items:center;gap:6px;white-space:nowrap}
.brands li::before{content:"";width:5px;height:5px;border-radius:50%;background:var(--blue);flex:none}
.web{position:absolute;left:24px;right:24px;bottom:56px;font-size:15px;font-weight:500;white-space:nowrap}
.web strong{color:var(--blue);font-weight:700}
</style>
</head>
<body>
<main class="flyer">
  <div class="brand"><span class="brand-mark"></span><span>Steadfast Corner<br>Vending</span></div>

  <div class="machines" role="img" aria-label="Photo of a snack vending machine beside a red cold-drink vending machine"></div>

  <div class="badge">
    <span class="badge-small">Special<br>pricing on</span>
    <span class="badge-big">Bulk<br>orders</span>
  </div>

  <div class="welcome">WELCOME TO</div>
  <h1 class="headline">
    <span class="dark">Steadfast</span>
    <span class="blue">Corner</span>
    <span class="blue">Vending</span>
  </h1>

  <p class="tagline">Our vending machine services are designed to cater to your every craving and refreshment need, all with a touch of modern convenience.</p>

  <div class="why">Why choose us?</div>

  <section class="reasons col-a">
    <div class="reason">
      <h3><svg viewBox="0 0 14 14"><rect x="1" y="2" width="10" height="10" rx="1.5" fill="none" stroke="currentColor" stroke-width="1.4"/><path d="M4 7l2.5 2.5L13 2" fill="none" stroke="currentColor" stroke-width="1.6"/></svg>Zero Cost to you</h3>
      <p>We provide state-of-the-art vending machines at NO COST TO YOU</p>
    </div>
    <div class="reason">
      <h3><svg viewBox="0 0 14 14"><rect x="1" y="2" width="10" height="10" rx="1.5" fill="none" stroke="currentColor" stroke-width="1.4"/><path d="M4 7l2.5 2.5L13 2" fill="none" stroke="currentColor" stroke-width="1.6"/></svg>Reliability</h3>
      <p>We are so passionate about being reliable that it is in our name. We are a small company that is HUGE on service. We are local owner/ operators that truly care about our most valuable asset - YOU, the customer.</p>
    </div>
    <div class="reason">
      <h3><svg viewBox="0 0 14 14"><rect x="1" y="2" width="10" height="10" rx="1.5" fill="none" stroke="currentColor" stroke-width="1.4"/><path d="M4 7l2.5 2.5L13 2" fill="none" stroke="currentColor" stroke-width="1.6"/></svg>Convenience</h3>
      <p>Say goodbye to time-consuming trips to the store. With our vending machines, your favorite snacks, drinks, and essentials are just a few steps away, available 24/7.</p>
    </div>
    <div class="reason">
      <h3><svg viewBox="0 0 14 14"><rect x="1" y="2" width="10" height="10" rx="1.5" fill="none" stroke="currentColor" stroke-width="1.4"/><path d="M4 7l2.5 2.5L13 2" fill="none" stroke="currentColor" stroke-width="1.6"/></svg>Quality</h3>
      <p>We stock our vending machines with high-quality, fresh products from trusted brands. You can trust that every selection you make is a delicious and satisfying choice.</p>
    </div>
  </section>

  <section class="reasons col-b">
    <div class="reason">
      <h3><svg viewBox="0 0 14 14"><rect x="1" y="2" width="10" height="10" rx="1.5" fill="none" stroke="currentColor" stroke-width="1.4"/><path d="M4 7l2.5 2.5L13 2" fill="none" stroke="currentColor" stroke-width="1.6"/></svg>Variety</h3>
      <p>We understand that different people have different tastes. That's why we offer a wide range of snacks, beverages, and everyday essentials, including healthy options, to satisfy every palate.</p>
    </div>
    <div class="reason">
      <h3><svg viewBox="0 0 14 14"><rect x="1" y="2" width="10" height="10" rx="1.5" fill="none" stroke="currentColor" stroke-width="1.4"/><path d="M4 7l2.5 2.5L13 2" fill="none" stroke="currentColor" stroke-width="1.6"/></svg>Customization</h3>
      <p>Tailor the vending machine offerings to your specific needs. We can customize our vending services to suit your preferences.</p>
    </div>
    <div class="reason">
      <h3><svg viewBox="0 0 14 14"><rect x="1" y="2" width="10" height="10" rx="1.5" fill="none" stroke="currentColor" stroke-width="1.4"/><path d="M4 7l2.5 2.5L13 2" fill="none" stroke="currentColor" stroke-width="1.6"/></svg>Technology</h3>
      <p>Our vending machines are equipped with state-of-the-art technology, making payments easy with a variety of options, including contactless payments and mobile apps.</p>
    </div>
    <div class="reason">
      <h3><svg viewBox="0 0 14 14"><rect x="1" y="2" width="10" height="10" rx="1.5" fill="none" stroke="currentColor" stroke-width="1.4"/><path d="M4 7l2.5 2.5L13 2" fill="none" stroke="currentColor" stroke-width="1.6"/></svg>On-time Maintenance</h3>
      <p>We take pride in keeping our vending machines in top condition. Our proactive maintenance team ensures that you always have a hassle-free experience.</p>
    </div>
  </section>

  <p class="call">Give us a call at
    <svg viewBox="0 0 20 20"><circle cx="10" cy="10" r="9.5" fill="var(--blue)"/><path d="M7 5.5c.6-.4 1.2 0 1.5.6l.7 1.5c.2.5 0 1-.4 1.3l-.6.4c.6 1.3 1.5 2.2 2.8 2.8l.4-.6c.3-.4.8-.6 1.3-.4l1.5.7c.6.3 1 .9.6 1.5-.6 1-1.8 1.5-2.9 1.1-3-1-5.4-3.4-6.4-6.4C5.5 7.3 6 6.1 7 5.5z" fill="#fff"/></svg>
    <strong>555-014-2290</strong></p>

  <aside class="services">
    <h2>OUR <strong>SERVICES</strong></h2>

    <div class="service">
      <svg viewBox="0 0 52 56" fill="none" stroke="var(--blue)" stroke-width="2"><rect x="4" y="2" width="40" height="50" rx="2"/><rect x="9" y="7" width="22" height="34"/><path d="M9 16h22M9 24h22M9 32h22M16 7v34M23 7v34"/><rect x="34" y="9" width="6" height="9"/><path d="M35 24h4M35 28h4M9 46h22M10 52v3M38 52v3"/></svg>
      <div>
        <h3>Vending</h3>
        <p>Our vending machine services are designed to cater to your every craving and refreshment need, all with a touch of modern convenience.</p>
      </div>
    </div>

    <div class="service">
      <svg viewBox="0 0 52 56" fill="none" stroke="var(--blue)" stroke-width="2"><rect x="4" y="4" width="34" height="48" rx="2"/><path d="M4 18h34"/><circle cx="12" cy="11" r="2.5"/><circle cx="21" cy="11" r="2.5"/><circle cx="30" cy="11" r="2.5"/><path d="M13 30h14v10a5 5 0 0 1-5 5h-4a5 5 0 0 1-5-5z"/><path d="M27 33h3a3 3 0 0 1 0 6h-3M42 10c3 3 3 7 0 10M47 7c4 5 4 11 0 16"/></svg>
      <div>
        <h3>Coffee Service</h3>
        <p>Indulge in a diverse selection of delicious coffees. Our team sources the finest brands, ensuring that each cup of coffee is a pleasurable journey. We offer a wide variety of options, including:</p>
        <ul class="brands">
          <li>Northbrew</li><li>Hillside Beans</li>
          <li>Morning Ring</li><li>Golden Grind</li>
          <li>Polar Roast</li><li>Homestead Blend</li>
          <li>Antler Coffee</li>
        </ul>
      </div>
    </div>

    <div class="service">
      <svg viewBox="0 0 52 56" fill="none" stroke="var(--blue)" stroke-width="2"><rect x="3" y="6" width="46" height="44" rx="1"/><path d="M26 6v44M3 28h46"/><rect x="8" y="11" width="6" height="12"/><rect x="16" y="14" width="6" height="9"/><rect x="31" y="11" width="6" height="12"/><rect x="39" y="15" width="6" height="8"/><rect x="8" y="34" width="14" height="11"/><rect x="31" y="33" width="6" height="12"/><rect x="39" y="36" width="6" height="9"/></svg>
      <div>
        <h3>Pantry Service</h3>
        <p>With innovative Pantry Services from Steadfast Corner Vending. Elevate the break room experience in your office with a customized selection of snacks, beverages, and kitchen essentials, all conveniently accessible in your workplace pantry.</p>
      </div>
    </div>

    <p class="web">www.<strong>steadfastcornervend</strong>.example</p>
  </aside>
</main>
</body>
</html>
```